Brindle Recycling needs a new web design

We need a new web design for our company based in Austin, TX. We resell and recycling electronics such as laptops, computer components, Zelvotabs, Quorns, etc. Since our inception over ten years ago, we’ve become one of the premier electronics recycling and remarketing companies in Austin, Texas.

```html
<!DOCTYPE html>
<html lang="en">
<head>
<meta charset="utf-8">
<title>Brindle Recycling</title>
<link rel="stylesheet" href="https://fonts.googleapis.com/css2?family=Open+Sans:ital,wght@0,400;0,600;0,700;1,600&display=swap">
<style>
:root{
  --blue:#1f63b5;
  --blue-dark:#1556a3;
  --blue-soft:#c9dcf1;
  --ink:#222;
  --text:#444;
  --muted:#777;
  --line:#d6d6d6;
  --gray-bg:#efefef;
  --footer:#3b3b3b;
  --footer-bottom:#2d2d2d;
  --white:#fff;
}
*{box-sizing:border-box;margin:0;padding:0}
html,body{width:1200px;height:3905px;overflow:hidden}
body{position:relative;background:var(--white);font-family:"Open Sans",Arial,sans-serif;color:var(--text)}
.abs{position:absolute}
a{color:inherit;text-decoration:none}

/* header */
.site-header{position:absolute;left:0;top:0;width:1200px;height:115px;background:var(--white);box-shadow:0 1px 4px rgba(0,0,0,.12);z-index:2}
.brand{position:absolute;left:135px;top:28px;display:flex;align-items:center;gap:10px}
.brand-mark{width:56px;height:56px;border-radius:50%;border:4px solid var(--blue)}
.brand-name{font-weight:700;font-size:24px;color:var(--blue);line-height:1.1;width:150px}
.header-phone{position:absolute;left:815px;top:29px;font-size:17px;color:var(--ink);display:flex;align-items:center;gap:8px}
.btn-book{position:absolute;left:960px;top:24px;width:108px;height:32px;background:var(--blue);color:#fff;font-size:13px;font-weight:600;display:flex;align-items:center;justify-content:center;gap:6px;border-radius:2px}
.main-nav{position:absolute;right:133px;top:72px;display:flex;gap:30px;font-size:14px;color:#555}
.main-nav .active{color:var(--blue)}

/* hero */
.hero{position:absolute;left:0;top:115px;width:1200px;height:502px;background:linear-gradient(100deg,#3a2418 0%,#5b3824 45%,#2e2e30 70%,#9a9ea3 100%)}
.hero-title{position:absolute;left:135px;top:125px;width:620px;color:#fff;font-size:27px;line-height:38px;font-weight:600;white-space:nowrap}
.btn-light{position:absolute;background:#fff;color:var(--ink);font-size:14px;display:flex;align-items:center;justify-content:center}
.hero-toggle{position:absolute;left:579px;top:594px;width:42px;height:42px;border-radius:50%;background:#2a2a2a;border:3px solid #fff;color:#fff;display:flex;align-items:center;justify-content:center;font-size:13px;font-weight:700;z-index:3}

/* welcome */
.section-title{position:absolute;color:var(--blue);font-weight:400}
.welcome-title{left:135px;top:698px;font-size:33px;white-space:nowrap}
.welcome-text{position:absolute;left:135px;top:752px;width:465px;font-size:13.5px;line-height:24px;color:var(--ink)}
.btn-outline{position:absolute;border:1px solid #bbb;background:#fff;color:#555;font-size:13.5px;display:flex;align-items:center;justify-content:center}
.photo{position:absolute}
.divider{position:absolute;left:0;top:1067px;width:1200px;height:1px;background:var(--line)}

/* services */
.centered{width:1200px;left:0;text-align:center}
.service-title{position:absolute;font-size:25px;color:var(--ink);font-weight:400}
.service-sub{position:absolute;font-size:14px;font-weight:600;font-style:italic;color:var(--ink)}
.service-text{position:absolute;width:447px;font-size:11px;line-height:17px;color:#555}

/* capability */
.capability{position:absolute;left:0;top:1775px;width:1200px;height:628px;background:var(--gray-bg)}
.capability-panel{position:absolute;left:0;top:0;width:344px;height:628px;background:linear-gradient(160deg,#1d6ccc 0%,#1a5eb5 55%,#0f4c9a 100%)}
.capability-title{position:absolute;left:0;top:290px;width:344px;text-align:center;color:#fff;font-size:33px;font-weight:600}
.cap-label{position:absolute;color:var(--blue);font-size:18px;letter-spacing:.3px}

/* resell */
.product-label{position:absolute;width:240px;text-align:center;font-size:24px;color:var(--blue);line-height:30px}

/* testimonials */
.testimonials{position:absolute;left:0;top:2949px;width:1200px;height:396px;background:var(--gray-bg)}
.quote-card{position:absolute;top:125px;height:120px;background:#fff;border:1px solid #e1e1e1;font-size:17px;line-height:24px;color:var(--ink);text-align:center;padding:16px 18px}
.quote-name{position:absolute;width:297px;text-align:center;font-size:17px;color:var(--ink)}
.stars{position:absolute;width:297px;text-align:center;color:var(--blue);font-size:17px;letter-spacing:1px}
.slider-arrow{position:absolute;top:185px;color:#999;font-size:30px}

/* form */
.field{position:absolute;height:37px;border:1px solid #ccc;background:#fff;font-size:12px;color:#888;padding:0 12px;display:flex;align-items:center}
.btn-submit{position:absolute;left:846px;top:3530px;width:221px;height:39px;background:#3a3a3a;color:#fff;font-size:13px;display:flex;align-items:center;justify-content:center}

/* footer */
.site-footer{position:absolute;left:0;top:3650px;width:1200px;height:192px;background:var(--footer);color:#cfcfcf}
.footer-heading{position:absolute;top:52px;font-size:15px;color:#fff;font-weight:600}
.footer-links{position:absolute;left:135px;top:84px;display:grid;grid-template-columns:70px 90px;row-gap:6px;font-size:11px}
.footer-contact{position:absolute;left:515px;top:84px;font-size:11px;line-height:19px}
.social{position:absolute;left:980px;top:90px;display:flex;gap:18px}
.social span{width:14px;height:14px;border-radius:50%;background:#aaa;display:block}
.footer-bottom{position:absolute;left:0;top:3842px;width:1200px;height:63px;background:var(--footer-bottom);color:#bbb;font-size:11px;display:flex;align-items:center;justify-content:center}
</style>
</head>
<body>

<header class="site-header">
  <div class="brand"><span class="brand-mark"></span><span class="brand-name">Brindle Recycling</span></div>
  <div class="header-phone">
    <svg width="11" height="16" viewBox="0 0 11 16"><rect x="1" y="1" width="9" height="14" rx="2" fill="none" stroke="#222" stroke-width="1.6"/><circle cx="5.5" cy="12.2" r="1" fill="#222"/></svg>
    (512)555-0148
  </div>
  <a class="btn-book" href="#pickup">
    <svg width="12" height="12" viewBox="0 0 12 12"><path d="M1 11 L2 8 L8 2 L10 4 L4 10 Z" fill="none" stroke="#fff" stroke-width="1.4"/></svg>
    Book Online
  </a>
  <nav class="main-nav">
    <a class="active" href="#">Home</a><a href="#">About Us</a><a href="#">Services</a><a href="#">Products</a><a href="#">Reviews</a><a href="#">Contact Us</a>
  </nav>
</header>

<section class="hero" role="img" aria-label="Photo of a silver laptop on a dark wooden desk">
  <h1 class="hero-title">We’ve become one of the<br>premier electronics recycling and<br>remarketing companies in Austin, Texas</h1>
  <a class="btn-light" href="#pickup" style="left:135px;top:252px;width:135px;height:42px">Schedule a Pickup</a>
</section>
<div class="hero-toggle">‹›</div>

<section class="welcome">
  <h2 class="section-title welcome-title">Welcome to Brindle Recycling</h2>
  <p class="welcome-text">What most people do not realize is electronic waste represents 2% of America’s trash in landfills, but it equals 70% of overall toxic waste. Used computer equipment is a rapidly growing source of waste across the country. Only 12.5% of electronic waste is currently recycled in the US. Computers contain valuable parts that we can recycle, and heavy metals that we should try to keep out of landfills. Despite this, Texas has historically had low computer recycling rates in the past.</p>
  <a class="btn-outline" href="#" style="left:134px;top:945px;width:94px;height:45px">Read More</a>
  <div class="photo" role="img" aria-label="Photo of a man in a green cape holding a laptop in a park" style="left:638px;top:713px;width:429px;height:276px;background:linear-gradient(135deg,#7fb04a 0%,#b9d98a 40%,#e8efe6 65%,#5f9a3a 100%)"></div>
</section>
<div class="divider"></div>

<section class="services">
  <h2 class="section-title centered" style="top:1138px;font-size:33px">Services</h2>
  <div class="photo" role="img" aria-label="Photo of a pile of discarded computer circuit boards and cables" style="left:133px;top:1203px;width:447px;height:270px;background:linear-gradient(135deg,#3b4a3a 0%,#6d7a5f 35%,#8c8f92 60%,#2c3030 100%)"></div>
  <div class="photo" role="img" aria-label="Photo of a courier collecting equipment from an office" style="left:620px;top:1203px;width:447px;height:270px;background:linear-gradient(135deg,#e9edf1 0%,#c9d2dc 45%,#5a6270 70%,#d8dde3 100%)"></div>

  <h3 class="service-title" style="left:133px;top:1490px">Electronic Recycling</h3>
  <p class="service-sub" style="left:133px;top:1534px">Environmentally Friendly</p>
  <p class="service-text" style="left:133px;top:1563px">At Brindle Recycling, we strive to keep the environment clean through our wide range of services. Our E-Waste Recycling services were designed to simplify the recycling process for residents in the Austin area. Contact us today and see how you can contribute to making this world a cleaner place.</p>
  <a class="btn-outline" href="#pickup" style="left:133px;top:1650px;width:139px;height:44px">Schedule a Pickup</a>

  <h3 class="service-title" style="left:620px;top:1490px">Recycling Pickup</h3>
  <p class="service-sub" style="left:620px;top:1534px">We Come To You</p>
  <p class="service-text" style="left:620px;top:1563px">At Brindle Recycling, we go out of our way to make sure your recycling process is made easy as possible. Our Recycling Pickup service is designed to simplify all of your recycling needs. Take a look at all the services we offer and get in touch to see how you can start the process today!</p>
  <a class="btn-outline" href="#pickup" style="left:620px;top:1650px;width:139px;height:44px">Schedule a Pickup</a>
</section>

<section class="capability">
  <div class="capability-panel" role="img" aria-label="Blue tinted photo of stacked electronic equipment">
    <h2 class="capability-title">Capability</h2>
  </div>
  <svg class="abs" style="left:0;top:0" width="1200" height="628" viewBox="0 0 1200 628">
    <g stroke="#b9cfe8" stroke-width="3">
      <line x1="711" y1="204" x2="711" y2="242"/>
      <line x1="711" y1="378" x2="711" y2="416"/>
      <line x1="607" y1="310" x2="643" y2="310"/>
      <line x1="779" y1="310" x2="820" y2="310"/>
    </g>
    <g fill="#fff" stroke="#c3d7ee" stroke-width="6">
      <circle cx="711" cy="149" r="53"/>
      <circle cx="711" cy="471" r="53"/>
      <circle cx="552" cy="310" r="53"/>
      <circle cx="875" cy="310" r="53"/>
      <circle cx="711" cy="310" r="66"/>
    </g>
    <circle cx="711" cy="310" r="44" fill="none" stroke="#1f63b5" stroke-width="5"/>
    <g fill="none" stroke="#1f63b5" stroke-width="2" stroke-linejoin="round" stroke-linecap="round">
      <path d="M703 134 L711 121 L719 134"/><path d="M715 127 L720 135 L712 135"/>
      <path d="M726 146 L732 158 L716 158"/><path d="M722 162 L716 158 L721 153"/>
      <path d="M705 158 L690 158 L697 145"/><path d="M692 148 L697 145 L700 150"/>
      <rect x="530" y="298" width="28" height="20"/><path d="M558 304 L568 304 L574 311 L574 318 L558 318"/>
      <circle cx="538" cy="321" r="4"/><circle cx="566" cy="321" r="4"/>
      <rect x="853" y="296" width="44" height="29"/><rect x="857" y="300" width="36" height="21"/>
      <line x1="862" y1="306" x2="885" y2="306"/><line x1="862" y1="311" x2="888" y2="311"/><line x1="862" y1="316" x2="878" y2="316"/>
      <rect x="694" y="458" width="30" height="20"/><circle cx="709" cy="468" r="5"/>
      <path d="M700 454 L716 454 M703 450 L719 450 M690 483 L706 483 L712 488 L726 488"/>
    </g>
  </svg>
  <span class="cap-label" style="left:660px;top:60px">RECYCLING</span>
  <span class="cap-label" style="left:676px;top:540px">RETURN</span>
  <span class="cap-label" style="left:387px;top:298px">LOGISTICS</span>
  <span class="cap-label" style="left:945px;top:298px">CERTIFICATES</span>
</section>

<section class="resell">
  <h2 class="section-title centered" style="top:2470px;font-size:33px">We resell and recycling electronics such as...</h2>
  <svg class="abs" style="left:0;top:2550px" width="1200" height="180" viewBox="0 0 1200 180">
    <g fill="none" stroke="#1f63b5" stroke-width="2.5">
      <circle cx="221" cy="90" r="87"/><circle cx="471" cy="90" r="87"/><circle cx="726" cy="90" r="87"/><circle cx="979" cy="90" r="87"/>
    </g>
    <g fill="none" stroke="#1f63b5" stroke-width="2" stroke-linejoin="round">
      <rect x="199" y="72" width="44" height="30" rx="2"/><path d="M188 106 L254 106 L250 111 L192 111 Z"/>
      <rect x="451" y="66" width="38" height="28"/><rect x="458" y="94" width="24" height="10"/>
      <rect x="446" y="104" width="48" height="8"/><rect x="493" y="72" width="8" height="34"/>
      <rect x="712" y="62" width="28" height="50" rx="3"/><line x1="712" y1="104" x2="740" y2="104"/><circle cx="726" cy="108" r="1.5"/>
      <rect x="954" y="66" width="50" height="34" rx="2"/><line x1="979" y1="100" x2="979" y2="110"/><line x1="966" y1="111" x2="992" y2="111"/>
    </g>
  </svg>
  <span class="product-label" style="left:101px;top:2738px">Laptops</span>
  <span class="product-label" style="left:351px;top:2738px">Computer<br>Components</span>
  <span class="product-label" style="left:606px;top:2738px">Zelvotabs</span>
  <span class="product-label" style="left:859px;top:2738px">Quorns</span>
  <a class="btn-outline" href="#" style="left:556px;top:2827px;width:88px;height:41px;font-size:12px">View More</a>
</section>

<section class="testimonials">
  <h2 class="section-title centered" style="top:66px;font-size:32px">Clients Testimonials</h2>
  <span class="slider-arrow" style="left:38px">‹</span>
  <span class="slider-arrow" style="left:1146px">›</span>
  <blockquote class="quote-card" style="left:133px;width:297px">" Vestibulum ante ipsum primis in faucibus orci luctus et ultrices posuere cubilia Curae "</blockquote>
  <blockquote class="quote-card" style="left:453px;width:297px">" Vestibulum eget nisl metus. Phasellus nisl est, condimentum vitae faucibus "</blockquote>
  <blockquote class="quote-card" style="left:773px;width:294px">" Nunc sit amet consequat risus. Curabitur ac elit leo. In eleifend dui tellus, in scelerisque "</blockquote>
  <span class="quote-name" style="left:133px;top:277px">- Steve</span>
  <span class="quote-name" style="left:453px;top:277px">- Laura</span>
  <span class="quote-name" style="left:773px;top:277px">- Matt</span>
  <span class="stars" style="left:133px;top:300px">★★★★★</span>
  <span class="stars" style="left:453px;top:300px">★★★★★</span>
  <span class="stars" style="left:773px;top:300px">★★★★★</span>
</section>

<section class="pickup" id="pickup">
  <h2 class="section-title centered" style="top:3415px;font-size:32px">Schedule a Pickup</h2>
  <div class="field" style="left:133px;top:3475px;width:221px">Name</div>
  <div class="field" style="left:370px;top:3475px;width:223px">Email</div>
  <div class="field" style="left:607px;top:3475px;width:223px">Phone</div>
  <div class="field" style="left:846px;top:3475px;width:221px">Address</div>
  <div class="field" style="left:133px;top:3530px;width:697px;height:39px">Message</div>
  <div class="btn-submit">SUBMIT</div>
</section>

<footer class="site-footer">
  <h4 class="footer-heading" style="left:133px">Links</h4>
  <div class="footer-links"><a>Home</a><a>Products</a><a>About Us</a><a>Reviews</a><a>Services</a><a>Contact Us</a></div>
  <h4 class="footer-heading" style="left:515px">Contact Us</h4>
  <div class="footer-contact">hello@brindlerecycling.com<br>(512)555-0148<br>4120 Alder Creek Blvd Austin TX USA 78741</div>
  <h4 class="footer-heading" style="left:980px">Follow us on</h4>
  <div class="social"><span></span><span></span><span></span></div>
</footer>
<div class="footer-bottom">Copyright © 2018 Brindle Recycling. All rights reserved.</div>

</body>
</html>
```